Web Design for an Innovative Life Science Marketplace

IMPORTANT:
The software is called CS-Cart. It has capabilities and limitations with design features in the software. There is a certain framework that needs to be followed. It is PHP and Linux. It may require add-ons for your design, so please be specific with what is required. It’s preferred the designer has CS-Cart knowledge/experience.

Key Requirements
1. I’d like the design to include an implemented/recommended CS-Cart theme that is consistent with our branding (see the marketing collateral and logo).
2. I then need the additional design changes to that theme to create the below web pages.
3. All designs should be consistent with our branding. All pictures should either be computer generated (clip art-like) or pictures of happy patients. What is a happy patient? Close up photo of someone healthy, happy, and experiencing/enjoying life. Not someone in a hospital or getting care. Please see examples already on the site.

Please see the attached Web Design details in the word document. That document is important to complete the design.

```html
<!DOCTYPE html>
<html lang="en">
<head>
<meta charset="utf-8">
<title>LoopSourceLS – Life Science Marketplace</title>
<link href="https://fonts.googleapis.com/css2?family=Oswald:wght@400;500;700&family=Roboto:wght@400;500;700&display=swap" rel="stylesheet">
<style>
:root{
  --green:#8cc63f;
  --green-dark:#7ab32f;
  --teal:#13866f;
  --teal-dark:#0f6f5c;
  --charcoal:#3a3a3a;
  --footer:#2d2d2d;
  --footer-bottom:#1e1e1e;
  --text:#333;
  --muted:#bbb;
  --white:#fff;
}
*{box-sizing:border-box;margin:0;padding:0}
html,body{width:1200px;height:3285px;overflow:hidden}
body{font-family:"Roboto",Arial,sans-serif;color:var(--text);background:var(--white);font-size:13px}
h1,h2,h3,h4{font-family:"Oswald",Arial,sans-serif;font-weight:700}
section,header,footer{position:relative;width:1200px}

/* top bar */
.topbar{height:30px;background:var(--teal);color:var(--white);font-size:11px}
.topbar .account{position:absolute;left:175px;top:8px;display:flex;gap:24px}
.topbar .search{position:absolute;left:765px;top:5px;width:135px;height:20px;border:1px solid #cfe;border-radius:2px;padding:3px 6px;font-size:10px;color:#dfe}
.topbar .cart{position:absolute;left:915px;top:8px;display:flex;align-items:center;gap:6px}
.topbar .cart i{display:block;width:16px;height:16px;border-radius:50%;background:var(--white)}

/* header */
.site-header{height:110px}
.brand{position:absolute;left:175px;top:38px;display:flex;align-items:center;gap:10px}
.brand .dot{width:34px;height:34px;border-radius:50%;background:var(--teal)}
.brand .name{font-family:"Oswald",sans-serif;font-weight:700;font-size:30px;color:var(--green)}
.main-nav{position:absolute;right:175px;top:47px;display:flex;gap:26px;font-size:12px;font-weight:500;color:#444}

/* hero */
.hero{height:523px;background:linear-gradient(180deg,#8fb86a 0%,#b9cf7d 45%,#d9d257 75%,#c7b932 100%)}
.hero .caption{position:absolute;left:175px;top:215px}
.hero .caption h3{display:inline-block;background:var(--green);color:var(--white);font-weight:500;font-size:20px;padding:8px 14px}
.hero .caption p{margin-top:6px;width:400px;background:rgba(40,40,40,.75);color:var(--white);font-size:11px;line-height:17px;padding:8px 14px}

/* who should join */
.join{height:537px;text-align:center}
.section-title{font-size:27px;color:#222;padding-top:40px}
.section-title::after{content:"";display:block;width:40px;height:3px;background:var(--green);margin:8px auto 0}
.intro{width:780px;margin:16px auto 0;font-size:12px;line-height:18px;color:#444}
.join-cards{position:absolute;top:175px;left:163px;display:flex;gap:32px}
.join-card{width:272px;height:302px;background:var(--green);color:var(--white);padding-top:36px}
.join-card.alt{background:var(--teal)}
.join-card .icon{width:76px;height:76px;border-radius:50%;background:var(--white);margin:0 auto;display:flex;align-items:center;justify-content:center}
.join-card h3{font-size:19px;margin-top:18px;font-weight:500}
.join-card p{font-size:12px;line-height:17px;margin:8px 26px 0;height:52px}
.join-card .btn{display:inline-block;margin-top:12px;background:var(--white);color:var(--teal);font-size:11px;font-weight:700;padding:9px 16px}

/* mission band */
.mission{height:232px;background:linear-gradient(90deg,#2f2f2f,#4a4a4a 50%,#2f2f2f);color:var(--white);text-align:center}
.mission h2{font-size:44px;padding-top:48px;letter-spacing:1px}
.mission p{font-size:21px;line-height:27px;margin-top:10px;color:#ddd;font-weight:400}

/* products */
.products-band{height:78px;background:var(--green);text-align:center}
.products-band h2{color:var(--white);font-size:33px;line-height:78px;font-weight:500}
.products-band::after{content:"";position:absolute;left:570px;bottom:-16px;border:30px solid transparent;border-top:16px solid var(--green);border-bottom:0}
.products{height:480px;text-align:center}
.products .intro{margin-top:0;padding-top:50px}
.product{position:absolute;top:128px;width:226px;text-align:center}
.product .disc{width:186px;height:186px;margin:0 auto;border-radius:50%;border:6px solid #ddd;overflow:hidden;position:relative;box-shadow:0 3px 6px rgba(0,0,0,.2)}
.product .disc .fill{position:absolute;inset:0}
.product .disc .label{position:absolute;left:0;right:0;bottom:0;height:60px;background:var(--teal);color:var(--white);font-size:12px;font-weight:500;padding-top:14px;line-height:15px}
.product p{font-size:12px;line-height:18px;margin-top:14px;color:#444}
.product .btn{display:inline-block;margin-top:16px;background:var(--teal);color:var(--white);font-size:11px;font-weight:700;padding:9px 14px}

/* marketing */
.marketing{height:385px;background:var(--charcoal);margin-top:0}
.marketing .photo{position:absolute;left:0;top:0;width:590px;height:385px;background:linear-gradient(120deg,#c98a4e,#e8c9a4 45%,#a0b05a 100%)}
.marketing .copy{position:absolute;left:643px;top:38px;width:455px;color:var(--white)}
.marketing h2{font-size:31px;font-weight:500}
.marketing p{font-size:10.5px;line-height:16px;margin-top:12px;color:#eee}
.marketing .actions{margin-top:22px;display:flex;gap:12px}
.marketing .actions span{border:1px solid #ccc;font-size:11px;padding:10px 14px}

/* promise */
.promise{height:510px}
.promise .box{position:absolute;left:160px;top:65px;width:880px;height:360px;background:var(--green)}
.promise .box h2{position:absolute;left:0;width:440px;top:86px;text-align:center;color:var(--white);font-size:30px;font-weight:500}
.promise .box p{position:absolute;left:0;width:440px;top:145px;text-align:center;color:var(--white);font-family:"Oswald",sans-serif;font-size:21px;line-height:32px;letter-spacing:.5px}
.promise .snapshot{position:absolute;left:625px;top:40px;width:380px;height:268px;background:var(--white);padding:10px;transform:rotate(6deg);box-shadow:0 4px 12px rgba(0,0,0,.3)}
.promise .snapshot div{width:100%;height:100%;background:linear-gradient(135deg,#c2d9ea,#e9d2b8 50%,#8fb0c9)}

/* newsletter */
.newsletter{height:80px;background:var(--teal);color:var(--white)}
.newsletter h4{position:absolute;left:152px;top:27px;font-family:"Roboto",sans-serif;font-weight:500;font-size:17px}
.newsletter .field{position:absolute;left:400px;top:27px;width:338px;height:27px;background:var(--white);color:#999;font-size:10px;padding:7px 10px}
.newsletter .submit{position:absolute;left:738px;top:27px;width:86px;height:27px;background:#222;font-size:11px;text-align:center;line-height:27px}
.newsletter .social{position:absolute;left:884px;top:27px;display:flex;gap:10px}
.newsletter .social span{width:26px;height:26px;background:var(--white)}

/* footer */
.site-footer{height:270px;background:var(--footer);color:var(--muted);font-size:11px}
.site-footer h4{font-family:"Roboto",sans-serif;font-weight:500;color:var(--white);font-size:16px}
.site-footer h4::after{content:"";display:block;width:40px;height:2px;background:var(--teal);margin-top:8px}
.col{position:absolute;top:40px}
.links{display:grid;grid-template-columns:170px 150px;margin-top:14px;row-gap:7px}
.links li{list-style:none}
.links li::before{content:"› ";color:var(--green)}
.quote{margin-top:18px;width:250px;border:1px solid #555;padding:14px;font-style:italic;line-height:16px}
.quote-by{margin-top:16px;color:var(--teal);font-size:11px}
.contact li{list-style:none;display:flex;align-items:center;gap:10px;margin-top:12px;line-height:15px}
.contact li.big{font-size:15px;color:#ddd}
.contact svg{flex:none}
.bottom-bar{height:50px;background:var(--footer-bottom);color:#ccc;font-size:11px}
.bottom-bar p{position:absolute;left:152px;top:18px}
.bottom-bar .pay{position:absolute;right:152px;top:15px;display:flex;gap:6px}
.bottom-bar .pay span{width:30px;height:20px;background:#e6e6e6;border-radius:2px}
</style>
</head>
<body>

<div class="topbar">
  <div class="account"><span>● Login</span><span>● Registration</span></div>
  <div class="search">Search here...</div>
  <div class="cart"><i></i>Cart: 0 items - $0.00</div>
</div>

<header class="site-header">
  <div class="brand"><span class="dot"></span><span class="name">LOOPSOURCELS</span></div>
  <nav class="main-nav"><span>HOME</span><span>ABOUT US</span><span>HOW IT WORKS</span><span>WHY LOOPSOURCELS</span><span>FAQ</span><span>CONTACT US</span></nav>
</header>

<section class="hero" role="img" aria-label="Happy woman with arms outstretched in a sunny meadow of yellow flowers">
  <div class="caption">
    <h3>JOIN THE CIRCULAR SUPPLY CHAIN</h3>
    <p>A virtual multi-vendor marketplace and for the life sciences community to connect and transact before and after-market materials and equipment</p>
  </div>
</section>

<section class="join">
  <h2 class="section-title">WHO SHOULD JOIN</h2>
  <p class="intro">Lorem Ipsum is simply dummy text of the printing and typesetting industry. Lorem Ipsum has been the industry's standard dummy survived not only five centuries, but also the leap into electronic typesetting, remaining essentially unchanged. It was popularised software like Quill PageSetter including versions</p>
  <div class="join-cards">
    <div class="join-card">
      <div class="icon"><svg width="40" height="40" viewBox="0 0 40 40"><rect x="8" y="8" width="24" height="28" fill="none" stroke="#8cc63f" stroke-width="3"/><path d="M14 15h4M22 15h4M14 22h4M22 22h4M17 36v-7h6v7" stroke="#8cc63f" stroke-width="3" fill="none"/></svg></div>
      <h3>MANUFACTURERS</h3>
      <p>Create an Account in Minutes to Sell/Buy Excess or Obsolete Materials and Equipment</p>
      <span class="btn">CLICK HERE ›</span>
    </div>
    <div class="join-card alt">
      <div class="icon"><svg width="40" height="40" viewBox="0 0 40 40"><circle cx="20" cy="20" r="15" fill="none" stroke="#13866f" stroke-width="3"/><path d="M5 20h30M20 5c-7 8-7 22 0 30M20 5c7 8 7 22 0 30" fill="none" stroke="#13866f" stroke-width="2.5"/></svg></div>
      <h3>RESEARCHERS</h3>
      <p>Sell/Buy Low-Cost Materials and Receive Donations</p>
      <span class="btn">CLICK HERE ›</span>
    </div>
    <div class="join-card">
      <div class="icon"><svg width="40" height="40" viewBox="0 0 40 40"><rect x="8" y="18" width="24" height="16" fill="none" stroke="#8cc63f" stroke-width="3"/><path d="M8 18l4-8h16l4 8M20 10v8" fill="none" stroke="#8cc63f" stroke-width="3"/></svg></div>
      <h3>ORIGINAL SUPPLIERS</h3>
      <p>Market Your Products Across a Broad Life Sciences Network</p>
      <span class="btn">CLICK HERE ›</span>
    </div>
  </div>
</section>

<section class="mission">
  <h2>LOOPSOURCELS</h2>
  <p>ASPIRES TO CHANGE THE WASTE AND RISK PARADIGM<br>IN THE LIFE SCIENCE INDUSTRY.</p>
</section>

<section class="products-band"><h2>OUR PRODUCTS</h2></section>
<section class="products">
  <p class="intro">Lorem Ipsum is simply dummy text of the printing and typesetting industry. Lorem Ipsum has been the industry's standard dummy survived not only five centuries, but also the leap into electronic typesetting, remaining essentially unchanged. It was popularised software like Quill PageSetter including versions</p>
  <div class="product" style="left:156px">
    <div class="disc"><div class="fill" role="img" aria-label="Molecule model rendering" style="background:radial-gradient(circle at 40% 35%,#d8ecf7,#7fb6d8 70%)"></div><div class="label">RAW MATERIALS</div></div>
    <p>Consumable and starting materials for API and intermediate manufacturing or research.</p>
    <span class="btn">VIEW DETAILS</span>
  </div>
  <div class="product" style="left:377px">
    <div class="disc"><div class="fill" role="img" aria-label="Laboratory equipment on a bench" style="background:radial-gradient(circle at 50% 35%,#f2f4f6,#a9bccb 75%)"></div><div class="label">EQUIPMENT</div></div>
    <p>Consumable and starting materials for API and intermediate manufacturing or research.</p>
    <span class="btn">VIEW DETAILS</span>
  </div>
  <div class="product" style="left:603px">
    <div class="disc"><div class="fill" role="img" aria-label="Pipette and sample tubes" style="background:radial-gradient(circle at 50% 35%,#fbe9c9,#e0a85a 75%)"></div><div class="label">PARTS</div></div>
    <p>Consumable and starting materials for API and intermediate manufacturing or research.</p>
    <span class="btn">VIEW DETAILS</span>
  </div>
  <div class="product" style="left:829px">
    <div class="disc"><div class="fill" role="img" aria-label="Two researchers working together in a lab" style="background:radial-gradient(circle at 50% 35%,#eef1f4,#9fb3c2 75%)"></div><div class="label">COLLABORATIVE<br>RELATIONSHIPS</div></div>
    <p>Consumable and starting materials for API and intermediate manufacturing or research.</p>
    <span class="btn">VIEW DETAILS</span>
  </div>
</section>

<section class="marketing">
  <div class="photo" role="img" aria-label="Smiling young woman embracing an older woman outdoors"></div>
  <div class="copy">
    <h2>MARKETING MATERIALS</h2>
    <p>Lorem Ipsum is simply dummy text of the printing and typesetting industry. Lorem Ipsum has been the industry's standard dummy text ever since the 1500s, when an unknown printer took a galley of type and scrambled it to make a type specimen book. It has survived not only five centuries, and more recently desktop publishing software Quill PageSetter including versions Lorem Ipsum.</p>
    <p>Lorem Ipsum is simply dummy text of the printing and typesetting industry. Lorem Ipsum has been the industry's standard dummy text ever since the 1500s, when an unknown printer took a galley of type and scrambled it to make a type specimen book. It has survived not only five centuries, but also the leap into electronic the release of Typeset sheets containing Lorem Ipsum passages, and more recently desktop publishing software Quill PageSetter including versions Lorem Ipsum.</p>
    <div class="actions"><span>READ OUR WHITE PAPER</span><span>READ OUR BROCHURE</span></div>
  </div>
</section>

<section class="promise">
  <div class="box">
    <h2>OUR PROMISE</h2>
    <p>A GREENER, MORE COST-EFFICIENT, AND<br>QUALITY-DRIVEN SUPPLY CHAIN THROUGH<br>A COLLABORATIVE LIFE SCIENCES<br>MARKETPLACE</p>
  </div>
  <div class="snapshot"><div role="img" aria-label="Smiling woman sitting on a swing"></div></div>
</section>

<section class="newsletter">
  <h4>SIGN UP FOR NEWSLETTER</h4>
  <div class="field">Your email address</div>
  <div class="submit">Subscribe</div>
  <div class="social"><span></span><span></span><span></span><span></span></div>
</section>

<footer class="site-footer">
  <div class="col" style="left:152px">
    <h4>Quick Links</h4>
    <ul class="links">
      <li>Home</li><li>Multi-Tools</li><li>About Us</li><li>Wish list (0)</li><li>How it Works</li><li>My account</li><li>Why LoopSourceLS</li><li>Shopping cart</li><li>FAQ</li><li>Checkout</li><li>Contact Us</li><li>Contact Us</li>
    </ul>
  </div>
  <div class="col" style="left:500px">
    <h4>Testimonials</h4>
    <p class="quote">“ Lorem Ipsum is simply dummy text of the Ipsum has been the industry's standard dummy text ever since unknown the leap into electronic typesetting. ”</p>
    <p class="quote-by">Dana Miles</p>
  </div>
  <div class="col" style="left:848px">
    <h4>Get in Location</h4>
    <ul class="contact">
      <li><svg width="12" height="16" viewBox="0 0 12 16"><path d="M6 0a6 6 0 0 0-6 6c0 4.5 6 10 6 10s6-5.5 6-10a6 6 0 0 0-6-6zm0 8.5A2.5 2.5 0 1 1 6 3.5a2.5 2.5 0 0 1 0 5z" fill="#bbb"/></svg>48 Harbor Row, Lorem City,<br>Loremsimply dummy CA 94000</li>
      <li><svg width="14" height="10" viewBox="0 0 14 10"><rect width="14" height="10" fill="#bbb"/><path d="M0 0l7 6 7-6" stroke="#2d2d2d" fill="none"/></svg>info@loopsourcels.com</li>
      <li class="big"><svg width="14" height="14" viewBox="0 0 14 14"><path d="M3 0l3 3-2 2c1 2 3 4 5 5l2-2 3 3-2 3C6 14 0 8 0 3z" fill="#bbb"/></svg>123-456-7890</li>
      <li class="big"><svg width="14" height="14" viewBox="0 0 14 14"><rect x="1" y="4" width="12" height="8" rx="1" fill="#bbb"/><rect x="3" y="1" width="8" height="4" fill="#bbb"/></svg>123-456-7890</li>
    </ul>
  </div>
</footer>

<div class="bottom-bar" style="position:relative">
  <p>© 2018 loopsourcels.com . All Right Reserved</p>
  <div class="pay"><span></span><span></span><span></span><span></span></div>
</div>

</body>
</html>
```